Lumra Learning Web Design Project

Who We are:
Lumra Learning is education information portal/ magazine, providing information about the Chinese and International education markets. Our aim is to help school principals improve there curriculum, and parents in understanding this curriculum.

Project Brief:
The site will include education news updates, educational services, curriculum developments and overseas study. We hope the site represents the cross cultural bridge between the west and east. The site will cover both the Sciences and Arts.

Note:
The logo design competition is also underway so we only need the website design

What We want:
This competition is for Design only no coding!
Design a home page based on Template 1,2 or 3. I only need to select one.
The design of an article page.

Optional
Design a Parvex Shutters metro style splash page.

Sites We like:
http://www.qv.com.cn/tonguebridge/default.aspx
http://www.dailyuniversitybulletin.co.uk/
http://kptz.sinocraftlearn.net/

Template Explanations:
Template 1-
The main information has a dynamic sliding category view that when clicked displays the relevant info.
In addition to the main upper menu it also has a left hand sliding menu that pops out on click or gesture

Template 2-
Has limited number of Articles most of the menus are drop downs from the top menu

Template 3-
No Top menu

Target Market(s)

Teachers, principals and parents

Industry/Entity Type

Education

Requirements
Should not have
• kindergarten preschool feel

```html
<!DOCTYPE html>
<html lang="en">
<head>
<meta charset="utf-8">
<title>Lumra Learning</title>
<link rel="stylesheet" href="https://fonts.googleapis.com/css2?family=Open+Sans:wght@400;600;700&family=Roboto+Condensed:wght@400;700&display=swap">
<style>
:root{
  --page:#ece8e1;
  --white:#ffffff;
  --red:#e23b33;
  --red-dark:#c02a23;
  --navy:#0f3a5c;
  --blue:#215a8c;
  --blue-band:rgba(24,70,120,.9);
  --green:#59b947;
  --green-text:#7cbe35;
  --ink:#222222;
  --foot:#ececec;
  --foot-text:#6a6a6a;
}
*{box-sizing:border-box;margin:0;padding:0}
html,body{width:1163px;height:1200px;overflow:hidden}
body{background:var(--page);font-family:"Open Sans",Arial,sans-serif;color:var(--ink);position:relative}
.site{position:absolute;left:128px;top:0;width:908px;height:1200px;background:var(--white);border-top:5px solid var(--navy);overflow:hidden}
.abs{position:absolute}
.brand{left:18px;top:38px;display:flex;align-items:center;gap:10px}
.brand-dot{width:34px;height:34px;border-radius:50%;background:var(--blue)}
.brand-name{font-size:22px;font-weight:600;color:var(--red)}
.search{left:645px;top:61px;width:240px;height:34px;background:#f1f1f1;border:1px solid #dcdcdc;font-size:12px;color:#a0a0a0;padding:9px 13px}
.search svg{position:absolute;right:10px;top:6px}
.nav{left:0;top:139px;width:908px;height:47px;display:flex;background:var(--red);border-top:1px solid var(--red-dark);border-bottom:1px solid var(--red-dark)}
.nav a{display:flex;align-items:center;justify-content:center;color:#fff;font-weight:700;font-size:14px;text-decoration:none;border-right:1px solid var(--red-dark)}
.nav a:last-child{border-right:0}
.sidebar{left:9px;top:198px;width:64px;height:397px;background:var(--blue)}
.sidebar svg{position:absolute;left:16px}
.social{left:23px;width:36px;height:20px}
.social span{display:block;width:18px;height:18px;border-radius:50%;margin:0 auto}
.slider{left:82px;top:199px;width:579px;height:250px;background:linear-gradient(180deg,#3e4a52 0%,#5a6870 45%,#2f3a40 100%)}
.slider-caption{left:82px;top:394px;width:525px;height:55px;background:var(--blue-band);color:#fff;font-family:"Roboto Condensed",Arial,sans-serif;font-size:19.5px;padding:0 19px;line-height:55px;white-space:nowrap;overflow:hidden}
.slider-arrow{left:607px;top:394px;width:54px;height:55px;background:rgba(200,200,200,.55);display:flex;align-items:center;justify-content:center}
.thumb{left:82px;width:285px}
.thumb-a{top:457px;height:138px;background:linear-gradient(135deg,#6f7a70 0%,#4b5652 50%,#2e3a3c 100%)}
.thumb-b{top:606px;height:138px;background:linear-gradient(180deg,#d8d8d4 0%,#b8b8b2 60%,#4a4642 100%)}
.drop{width:36px;height:36px;background:#2a2d30;display:flex;align-items:center;justify-content:center}
.thumb-caption{left:82px;top:707px;width:285px;height:37px;background:var(--red);color:#fff;font-size:13px;line-height:37px;padding:0 13px;white-space:nowrap}
.thumb-caption .drop{position:absolute;right:0;top:0;height:37px;background:rgba(190,190,190,.85)}
.welcome{left:376px;top:457px;width:285px;height:287px;background:#ececec;padding:11px 12px 0 13px;overflow:hidden}
.welcome h2{font-weight:400;font-size:18.5px;color:#111;margin-bottom:5px;white-space:nowrap}
.welcome p{font-size:10.8px;line-height:20px;color:#8a8a8a;padding-left:2px}
.btn{display:inline-block;margin-top:8px;margin-left:2px;background:var(--red);color:#fff;font-size:13.5px;line-height:28px;padding:0 20px;width:116px}
.cats{left:82px;width:579px;height:52px;border:1px solid #cfcfcf;background:linear-gradient(180deg,#fff 0%,#f4f4f4 70%,#e4e4e4 100%);display:flex}
.cats span{flex:1;display:flex;align-items:center;justify-content:center;font-size:18px;color:var(--navy)}
.promo{left:671px;top:199px;width:227px;height:726px;background:linear-gradient(180deg,#fff 0%,#fff 30%,#c8ccd0 40%,#5c6e84 55%,#3d5066 70%,#7a7d80 80%,#7d8a86 100%)}
.promo-bar{left:671px;top:199px;width:227px;height:17px;background:var(--green)}
.promo-text{left:687px;top:262px;width:205px;font-family:"Roboto Condensed",Arial,sans-serif}
.promo-text .k1{font-size:35px;font-weight:700;color:#666;line-height:34px;letter-spacing:-.5px;white-space:nowrap}
.promo-text .k2{font-size:62px;font-weight:700;color:var(--green-text);line-height:56px;letter-spacing:-1px}
.promo-text p{font-size:14px;line-height:16px;color:#444;margin-top:12px;letter-spacing:-.3px}
.promo-text .cta{font-family:"Open Sans",Arial,sans-serif;font-size:10.5px;color:#43a333;margin-top:9px;white-space:nowrap}
.footer{left:0;top:937px;width:908px;height:223px;background:var(--foot)}
.fcol{top:974px}
.fcol h4{font-weight:400;font-size:13px;color:#222;margin-bottom:10px}
.fcol li{list-style:none;font-size:11.5px;line-height:16.4px;color:var(--foot-text);white-space:nowrap}
.fcol .gap{height:8px}
.bottom{left:0;top:1160px;width:908px;height:35px;background:linear-gradient(180deg,#4a4a4a,#2f2f2f);color:#fff;font-size:10px;font-weight:700;display:flex;justify-content:space-between;align-items:center;padding:0 21px}
</style>
</head>
<body>
<div class="site">
  <div class="abs brand"><span class="brand-dot"></span><span class="brand-name">Lumra Learning</span></div>
  <div class="abs search">Search Site
    <svg width="20" height="20" viewBox="0 0 20 20"><circle cx="8" cy="8" r="6" fill="none" stroke="#777" stroke-width="2.4"/><line x1="12.5" y1="12.5" x2="18" y2="18" stroke="#777" stroke-width="3" stroke-linecap="round"/></svg>
  </div>

  <nav class="abs nav">
    <a style="width:111px">Home</a><a style="width:128px">About Us</a><a style="width:115px">Service</a><a style="width:149px">New &amp; Event</a><a style="width:97px">Blog</a><a style="width:172px">Lumra Learning</a><a style="width:136px">Contact Us</a>
  </nav>

  <div class="abs sidebar">
    <svg style="top:17px" width="32" height="32" viewBox="0 0 32 32"><path d="M3 16 L16 4 L29 16" fill="none" stroke="#fff" stroke-width="3.5"/><path d="M7 15 V29 H13 V21 H19 V29 H25 V15" fill="none" stroke="#fff" stroke-width="3.5"/></svg>
    <svg style="top:72px" width="32" height="32" viewBox="0 0 32 32"><circle cx="16" cy="16" r="14" fill="#fff"/><rect x="14" y="13" width="4" height="11" fill="#215a8c"/><circle cx="16" cy="9" r="2.3" fill="#215a8c"/></svg>
    <svg style="top:129px" width="32" height="32" viewBox="0 0 32 32"><path d="M5 27 L20 12" stroke="#fff" stroke-width="5" stroke-linecap="round"/><circle cx="23" cy="9" r="6" fill="#fff"/><path d="M7 5 L27 25" stroke="#fff" stroke-width="4" stroke-linecap="round"/></svg>
    <svg style="top:184px" width="32" height="32" viewBox="0 0 32 32"><rect x="4" y="5" width="26" height="22" fill="none" stroke="#fff" stroke-width="2.5"/><rect x="8" y="9" width="9" height="7" fill="#fff"/><path d="M20 10 H26 M20 14 H26 M8 19 H26 M8 23 H26" stroke="#fff" stroke-width="2"/></svg>
    <svg style="top:240px" width="32" height="32" viewBox="0 0 32 32"><ellipse cx="22" cy="9" rx="9" ry="6" fill="none" stroke="#fff" stroke-width="2.5"/><circle cx="11" cy="17" r="5" fill="#fff"/><path d="M2 31 Q11 19 20 31 Z" fill="#fff"/></svg>
    <svg style="top:295px" width="32" height="32" viewBox="0 0 32 32"><circle cx="16" cy="16" r="12" fill="none" stroke="#fff" stroke-width="4"/></svg>
    <svg style="top:352px" width="32" height="32" viewBox="0 0 32 32"><rect x="3" y="9" width="26" height="17" fill="#fff"/><path d="M3 9 L16 19 L29 9" fill="none" stroke="#215a8c" stroke-width="2"/></svg>
  </div>
  <div class="abs social" style="top:616px"><span style="background:#f39a2b"></span></div>
  <div class="abs social" style="top:662px"><span style="background:#2d4f8a"></span></div>
  <div class="abs social" style="top:708px"><span style="background:#3b6fc0"></span></div>
  <div class="abs social" style="top:755px"><span style="background:#1aa3e0"></span></div>
  <div class="abs social" style="top:801px"><span style="background:#5fc4e0"></span></div>
  <div class="abs social" style="top:847px"><span style="background:#e8357b"></span></div>
  <div class="abs social" style="top:894px"><span style="background:#42a9e0"></span></div>

  <div class="abs slider" role="img" aria-label="Photo of students raising their hands in front of a chalkboard"></div>
  <div class="abs slider-caption">Dolore eu feugiat nulla facilisis at vero eros et accumsan et</div>
  <div class="abs slider-arrow"><svg width="20" height="28" viewBox="0 0 20 28"><path d="M15 3 L5 14 L15 25" fill="none" stroke="#444" stroke-width="2.5"/></svg></div>

  <div class="abs thumb thumb-a" role="img" aria-label="Photo of a teacher at the board with a raised student hand in front"></div>
  <div class="abs drop" style="left:331px;top:559px"><svg width="14" height="9" viewBox="0 0 14 9"><path d="M1 1 L7 7 L13 1" fill="none" stroke="#fff" stroke-width="2"/></svg></div>
  <div class="abs thumb thumb-b" role="img" aria-label="Photo of a lecturer in front of a whiteboard with formulas and a class"></div>
  <div class="abs thumb-caption">Pas fait que survivre cinq siècles.<div class="drop"><svg width="14" height="9" viewBox="0 0 14 9"><path d="M1 1 L7 7 L13 1" fill="none" stroke="#0f3a5c" stroke-width="2"/></svg></div></div>

  <div class="abs welcome">
    <h2>Welcome to Lumra Learning</h2>
    <p>Le Lorem Ipsum est le faux texte standard de l'imprimerie depuis les années 1500, quand un peintre anonyme assembla ensemble des morceaux de texte pour réaliser un livre men de polices de texte. Il n'a pas fait que survivre cinq siècles, mais s'est aussi adapté tique informatique, sans que son contenu n'en soit modifié. Popularisé dans les années 1960 grâce à la vente de feuilles Letraset contenant des passages Lorem.</p>
    <span class="btn">Read More</span>
  </div>

  <div class="abs cats" style="top:754px"><span>Europe</span><span>Drama</span></div>
  <div class="abs cats" style="top:814px"><span>Asia</span><span>Science</span></div>
  <div class="abs cats" style="top:873px"><span>USA</span><span>English</span></div>

  <div class="abs promo" role="img" aria-label="Photo of rooftop solar panels on a factory building"></div>
  <div class="abs promo-bar"></div>
  <div class="abs promo-text">
    <div class="k1">WE'RE SAVING</div>
    <div class="k2">ENERGY</div>
    <p>Harwick's manufacturing facilities in Windsor comprise one of the largest solar installations of its kind in Ontario.</p>
    <div class="cta">CLICK TO SEE OUR ENERGY SAVINGS</div>
  </div>

  <div class="abs footer"></div>
  <div class="abs fcol" style="left:48px"><h4>COMPANY</h4><ul><li>Lorem Ipsum</li><li>Est simplement du</li><li>Faux texte employé</li><li>Dans la sition et la</li><li>Misen page avant</li><li>Impression</li></ul></div>
  <div class="abs fcol" style="left:214px"><h4>DISIGN GUIDES</h4><ul><li>Lorem Ipsum est simplement</li><li>Du faux texte employé dans</li><li>Sition et la misen page avant</li><li>Le Lorem Ipsum est le faux</li><li>Texte standard de l'imprimerie</li><li>Quand un peintre anonyme</li></ul></div>
  <div class="abs fcol" style="left:462px"><h4>INTERACT WITH US</h4><ul><li>Like us on Pagebook</li><li>Follow us on Chirper</li><li>News</li></ul><div class="gap"></div><h4>MORE INFORMATION</h4><ul><li>Brochures</li><li>videos</li><li>News</li></ul></div>
  <div class="abs fcol" style="left:706px"><h4>CONTACT US</h4><ul><li>Lumra Learning</li><li>48 Tamsin Lane</li><li>Australia</li><li>W12 7QT</li></ul><div class="gap"></div><ul><li>Tel: (0) 20 5550 1423</li><li>Fax: (0) 20 5550 1424</li></ul><div class="gap"></div><ul><li>hello@lumralearning.example</li></ul></div>

  <div class="abs bottom"><span>Copyright 2012 Website Name. All Rights Reserved.</span><span>Privacy Policy | Terms &amp; Condition</span></div>
</div>
</body>
</html>
```